Systems and Technology Consultants - Website

Design & Build a website for a new company which operates in the Systems and Technology space for Transportation, Government and Commercial sectors.

Overall design should be minimalist in nature.
Should also have a feed that provides news and event updates on the main page.
Logo has already been awarded and should be incorporated into the site.

We like the overall layout, functionality and simplicity of the below sites. Submitted designs could be similar to or a combination of the aspects on these sites, or perhaps a whole different concept - we are open to new ideas.
Norvique.com
Teblo.it

Update 1 Dated 27 May 2014

All I am moving away from the Teblo.it website and would like it to be more aligned with Norvique.com not only in layout but in functionality. I will be extending the deadline of this design brief for two weeks to incorporate additional requirements and will add addtional funding to the project.

Apologies for not having more information available to provide but with so many submissions its getting confusing.

Thanks Derek

Please note that the brief has been updated and the deadline has been extended.

Important: We will need two language versions of the website, English and Arabic; the website is hosted on HostPelican

Hello All, Thank you for your submissions. We have narrowed it down to the final 6 designers and I just wanted to take a moment and provide a bit of feedback regarding the concepts that we like and the modifications we are looking for. First, let me mention some of the design functions we like. - At the top of the homepage we really like the "region" or "language" tab so that the website can be viewed in both English and Arabic. - We like the homepage to have clear color variation so that the different sections of the homepage are distinct. Additionally, we like the bottom portion of the homepage to be in red. We feel that draws attention to our contact information. Again, we would like the colors to integrate black, gray-scale, red, etc. - Having a search tab at the top of the home page, or integrated into the main image, so that the site is easy to navigate. - We especially like the main image to have the scrolling tabs at the bottom so it is easy to browse the services offered (Consultancy, Solutions Architecture, Masters Systems Integration, Independent Design Review). - In regards to the services offered tab we really like the idea that a few people presented that have the outside of our logo with an icon in the middle of consultancy, solutions, etc., etc. Secondly, as mentioned in our brief we really enjoy the design of norvique site. Specially, we enjoy the strong iconic images they use, the way the tabs at the top scroll easily, and contact us page that generates an email. Lastly, I've included some photos of the concept we have been working on. What we are trying to demonstrate is how our company offers a range of services that are essentially linked together. We provide individual services that when combined present the full service package. We would like this concept to be integrated into the over concept of our website. Please feel free to ask for clarification of any of the above points or contact us if you have any additional questions. We appreciate all of your hard work and are very excited to see the updated designs. Best, Marta Vennick Quelbrant Senior Program Manager marta.vennick@quelbrant-example.com

Industry/Entity Type

Government

Font styles to use
Serif
Sans Serif

Requirements
Must have
• Must work on/adapt to various/mobile devices (responsive)
Must be simple and straightforward
Colors should be in line/matching with logo
2 language versions: English and Arabic (no Thai)
Services should be the first group/row of items after/below the main image
Note: the website will be hosted by hostpelican
Nice to have
• Submit feedback form
What's New section
The banner at the bottom of the site should not be too large; we would like a narrow one more
It would be nice if the header/top banner (with Home, About, etc. tabs) could stay in place as you scroll down (like Norvique and Chatterloop)
We will likely only use one image with a Company slogan on the Home page rather than a carousel of images to rotate through
Should not have
• This is the existing website: http://www.quelbrant-example.org
We do not like the animation, the way the banner icons/titles bounce
Not simple enough, we don't like the functionality or how pages load so slowly
We do not like the logo centered - it should be at the left
The banner and its tabs should not be towards the right, we would like them to be centered, to go all the way across and to be below the logo

```html
<!DOCTYPE html>
<html lang="en">
<head>
<meta charset="utf-8">
<title>Quelbrant International</title>
<link rel="stylesheet" href="https://fonts.googleapis.com/css2?family=Open+Sans:wght@300;400;600;700&display=swap">
<style>
:root{
  --red:#e3232b;
  --ink:#1c1c1c;
  --text:#5a5a5a;
  --muted:#8a8a8a;
  --card:#efefef;
  --band:#363a42;
  --white:#ffffff;
  --rule:#cfcfcf;
}
*{box-sizing:border-box;margin:0;padding:0}
html,body{width:941px;height:1200px;overflow:hidden}
body{position:relative;font-family:"Open Sans",Arial,sans-serif;color:var(--ink);background:var(--white)}
.abs{position:absolute}

/* hero */
.hero{left:0;top:0;width:941px;height:457px;overflow:hidden}
.hero-photo{position:absolute;inset:0;
  background:linear-gradient(90deg,#f4f6f7 0%,#eef1f3 30%,#d9dcdf 48%,#a9abae 62%,#8d8f93 78%,#c9ccd0 100%);}
.hero-photo::after{content:"";position:absolute;left:0;right:0;bottom:0;height:120px;
  background:linear-gradient(180deg,rgba(255,255,255,0),rgba(120,120,124,.25))}
.brand{display:flex;align-items:center;gap:10px;left:86px;top:20px}
.brand-dot{width:28px;height:28px;border-radius:50%;background:var(--red);flex:none}
.brand-name{font-weight:700;font-size:15px;letter-spacing:2.5px;color:var(--ink);line-height:1.1;white-space:nowrap}
.nav{left:410px;top:33px;display:flex;gap:0;font-size:11px}
.nav a{color:var(--ink);text-decoration:none;margin-right:28px}
.nav a.is-active{color:var(--red)}
.nav a:last-child{margin-right:0}
.hero-title{left:86px;top:178px;font-size:32px;font-weight:300;color:#222;display:flex;align-items:center;gap:10px}
.hero-title .accent{background:var(--white);color:var(--red);font-weight:700;padding:0 8px;line-height:40px}
.hero-lede{left:86px;top:236px;width:320px;font-size:11px;line-height:22px;color:#2a2a2a}
.btn{left:86px;top:300px;width:109px;height:28px;background:var(--red);color:var(--white);
  font-size:12px;font-weight:600;display:flex;align-items:center;justify-content:center;border-radius:2px}

/* intro */
.rule-red{width:52px;height:2px;background:var(--red)}
.section-title{font-size:19px;font-weight:400;color:#111}
.about{left:86px;top:484px;width:440px}
.about .section-title{margin-top:9px}
.about p{margin-top:14px;font-size:11px;line-height:18.8px;color:var(--text)}
.divider{left:536px;top:483px;width:1px;height:151px;background:var(--rule)}
.news{left:560px;top:484px;width:290px}
.news .section-title{margin-top:9px}
.news-dots{position:absolute;right:0;top:14px;display:flex;gap:4px}
.news-dots span{width:14px;height:14px;border-radius:50%;border:1.5px solid #b3b3b3}
.news-dots span.is-current{border-color:var(--red)}
.news-date{margin-top:13px;font-size:10.5px;color:var(--red)}
.news p{margin-top:9px;font-size:11px;line-height:21.5px;color:var(--text)}

/* sectors + services band */
.band{left:0;top:866px;width:941px;height:263px;background:var(--band)}
.sectors{left:86px;top:678px;width:769px;height:219px;display:flex}
.sector-text{width:192px;height:219px;background:var(--card);padding:22px 10px 0 17px;position:relative;z-index:2}
.sector-text::after{content:"";position:absolute;right:-12px;top:44px;border-style:solid;
  border-width:12px 0 12px 12px;border-color:transparent transparent transparent var(--card)}
.sector-text .section-title{margin-top:8px;font-size:19px}
.sector-text p{margin-top:12px;font-size:10.5px;line-height:18.8px;color:var(--muted)}
.sector-photo{width:192px;height:219px}
.photo-gov{background:linear-gradient(180deg,#4b4640 0%,#8c8375 45%,#d7cdbd 70%,#7a6f60 100%)}
.photo-com{background:linear-gradient(135deg,#eef1f4 0%,#b8c8da 40%,#6d7e93 70%,#e6e6e6 100%)}

.services-head{left:0;top:916px;width:941px;text-align:center}
.services-head .rule-red{margin:0 auto}
.services-head h2{margin-top:6px;font-size:23px;font-weight:300;color:var(--white)}
.services{left:86px;top:975px;width:769px;display:flex;justify-content:space-between;padding:0 10px}
.service{display:flex;flex-direction:column;align-items:center;color:var(--white);font-size:14px;font-weight:300}
.service svg{width:54px;height:54px;margin-bottom:20px}

/* footer */
.footer-brand{left:86px;top:1149px;gap:8px}
.footer-brand .brand-name{font-size:11px;letter-spacing:2px}
.footer-brand .brand-dot{width:22px;height:22px}
.social{left:256px;top:1157px;display:flex;gap:4px}
.social span{width:12px;height:12px;border-radius:50%;background:#c9c9c9}
.copyright{right:89px;top:1152px;font-size:10.5px;color:#7a7a7a}
</style>
</head>
<body>

<header class="hero abs">
  <div class="hero-photo" role="img" aria-label="Engineers in grey work jackets meeting around a table in a bright office, a yellow hard hat in front"></div>
  <div class="brand abs">
    <span class="brand-dot"></span>
    <span class="brand-name">QUELBRANT<br>INTERNATIONAL</span>
  </div>
  <nav class="nav abs">
    <a class="is-active" href="#">Home</a>
    <a href="#">Business Units</a>
    <a href="#">Services</a>
    <a href="#">About Us</a>
    <a href="#">Locations</a>
    <a href="#">Contact Us</a>
  </nav>
  <h1 class="hero-title abs">Welcome To <span class="accent">Quelbrant</span></h1>
  <p class="hero-lede abs">Lorem ipsum dolor sit amet, consectetuer adipiscing elit, sed diam nonummy nibh euismod tincidunt ut laoreet dolore</p>
  <a class="btn abs">Read More</a>
</header>

<section class="about abs">
  <div class="rule-red"></div>
  <h2 class="section-title">About Quelbrant International</h2>
  <p>Lorem ipsum dolor sit amet, consectetuer adipiscing elit, sed diam nonummy nibh euis-mod tincidunt ut laoreet dolore magna aliquam erat volutpat. Ut wisi enim ad minim veniam, quis nostrud exerci tation ullamcorper suscipit lobortis nisl ut aliquip ex ea com-modo consequat. Duis autem vel eum iriure dolor in hendrerit in vulputate velit esse molestie consequat</p>
</section>
<div class="divider abs"></div>
<section class="news abs">
  <div class="rule-red"></div>
  <h2 class="section-title">Latest News</h2>
  <div class="news-dots"><span></span><span></span><span class="is-current"></span><span></span></div>
  <div class="news-date">17-06-2014</div>
  <p>Lorem ipsum dolor sit amet, consectetuer adipiscing elit, sed diam nonummy nibh euismod tincidunt ut laoreet dolore magna aliquam erat volutpat.</p>
</section>

<div class="band abs"></div>

<section class="sectors abs">
  <article class="sector-text">
    <div class="rule-red"></div>
    <h3 class="section-title">Government</h3>
    <p>Lorem ipsum dolor sit amet, consectetuer adipiscing elit, sed diam nonummy nibh euismod tincidunt ut laoreet dolore magna aliquam erat volutpat. minim veniam, quis nostrud</p>
  </article>
  <div class="sector-photo photo-gov" role="img" aria-label="Marble hall lined with tall columns"></div>
  <article class="sector-text">
    <div class="rule-red"></div>
    <h3 class="section-title">Commercial</h3>
    <p>Lorem ipsum dolor sit amet, consectetuer adipiscing elit, sed diam nonummy nibh euismod tincidunt ut laoreet dolore magna aliquam erat volutpat. minim veniam, quis nostrud</p>
  </article>
  <div class="sector-photo photo-com" role="img" aria-label="Two engineers in hard hats reviewing building plans"></div>
</section>

<section class="services-head abs">
  <div class="rule-red"></div>
  <h2>Our Services</h2>
</section>

<section class="services abs">
  <div class="service">
    <svg viewBox="0 0 54 54" fill="none" stroke="#fff" stroke-width="4" stroke-linecap="round"><path d="M18 8l28 28-8 8L10 16z"/><path d="M6 30a16 16 0 0 0 18 18"/></svg>
    Telicommunications
  </div>
  <div class="service">
    <svg viewBox="0 0 54 54" fill="#fff"><rect x="22" y="6" width="10" height="6"/><rect x="25" y="10" width="4" height="8"/><rect x="6" y="18" width="42" height="30"/><g fill="#363a42"><rect x="10" y="28" width="3" height="14"/><rect x="16" y="28" width="3" height="14"/><rect x="22" y="28" width="3" height="14"/><rect x="28" y="28" width="3" height="14"/><rect x="34" y="28" width="3" height="14"/><rect x="40" y="28" width="3" height="14"/></g></svg>
    Airports
  </div>
  <div class="service">
    <svg viewBox="0 0 54 54" fill="#fff"><rect x="4" y="22" width="14" height="28"/><rect x="20" y="14" width="8" height="36"/><rect x="30" y="6" width="8" height="44"/><rect x="40" y="18" width="10" height="32"/><circle cx="12" cy="38" r="3" fill="#363a42"/></svg>
    Water Treatment Plants
  </div>
  <div class="service">
    <svg viewBox="0 0 54 54" fill="#fff"><rect x="14" y="4" width="26" height="4"/><rect x="10" y="10" width="34" height="32" rx="5"/><rect x="14" y="14" width="26" height="10" fill="#363a42"/><circle cx="18" cy="34" r="3" fill="#363a42"/><circle cx="36" cy="34" r="3" fill="#363a42"/><path d="M14 44l-4 8h4l3-6h20l3 6h4l-4-8z"/></svg>
    Rails
  </div>
  <div class="service">
    <svg viewBox="0 0 54 54" fill="#fff"><path d="M4 50V26l12 8v-8l12 8v-8l12 8V14h10v36z"/><path d="M8 16c6-8 14-8 20-4-6 0-10 2-12 6z"/><rect x="12" y="38" width="5" height="5" fill="#363a42"/><rect x="24" y="38" width="5" height="5" fill="#363a42"/></svg>
    Oil And Gas
  </div>
  <div class="service">
    <svg viewBox="0 0 54 54" fill="none" stroke="#fff" stroke-width="5" stroke-linecap="round"><circle cx="27" cy="9" r="5"/><path d="M27 14v34"/><path d="M20 20h14"/><path d="M6 28c0 12 10 20 21 20s21-8 21-20"/></svg>
    Ports
  </div>
</section>

<footer>
  <div class="brand footer-brand abs">
    <span class="brand-dot"></span>
    <span class="brand-name">QUELBRANT<br>INTERNATIONAL</span>
  </div>
  <div class="social abs"><span></span><span></span><span></span><span></span></div>
  <p class="copyright abs">Copyright 2005-2014 www.quelbrant-example.biz All rights reserved</p>
</footer>

</body>
</html>
```